Marrowby Water Taxi and Transport Business Card

I need business cards for my new water taxi and freight transport business I have started here in Kodiak Alaska. Kodiak is a remote island in the middle of the gulf of Alaska. There are seven native villages around the island and Kodiak is the #2 fishing port in the United States. We also have the largest Coast Guard Base in the U.S. My company will be providing water taxi and freight transport logistics to the villages and many hunting and fishing lodges as well as remote properties around the island.

I would like a business card that isn't status quo, something that stands out, either in feel or appearance. I do like clean minimal designs but it needs to have the necessary contact info on it.

Target Market(s)

remote lodge / property owners, residents of the many villages around Kodiak and any one wanting to enjoy the great outdoors of Kodiak Alaska

Industry/Entity Type

Business

Contact Information for Business Card

I like clean simple designs that aren't cluttered but still provide the necessary information

Colors
0255a3
3277b5
33a4d5
9bcb3c
add136
fbed22
ffc214
f78f20
f37122

Requirements
Must have
• logo and contact info
• Captain Mason Elwick
• www.marrowbyferryline.com
• mason@marrowbyferryline.com

```html
<!DOCTYPE html>
<html lang="en">
<head>
<meta charset="utf-8">
<title>Marrowby Water Taxi and Transport – Business Card</title>
<link href="https://fonts.googleapis.com/css2?family=Open+Sans:wght@400;700&display=swap" rel="stylesheet">
<style>
  :root {
    --navy: #0a2f7a;
    --deep-blue: #0255a3;
    --mid-blue: #3277b5;
    --sky-blue: #33a4d5;
    --sun-orange: #f8a13a;
    --snow: #ffffff;
    --stage: #e9ecef;
    --text-light: #ffffff;
    --text-soft: #dce9f7;
  }
  * { box-sizing: border-box; margin: 0; padding: 0; }
  html, body { width: 1200px; height: 913px; overflow: hidden; }
  body {
    background: var(--stage);
    font-family: "Open Sans", Arial, sans-serif;
    position: relative;
  }
  .card {
    position: absolute;
    width: 560px;
    height: 320px;
    border-radius: 4px;
    overflow: hidden;
    background: linear-gradient(160deg, var(--mid-blue) 0%, var(--deep-blue) 55%, var(--navy) 100%);
    box-shadow: 0 10px 24px rgba(0, 0, 0, 0.18);
  }
  .card--front { left: 50px; top: 110px; }
  .card--back { left: 590px; top: 480px; }

  .brand {
    position: absolute;
    left: 34px;
    top: 150px;
    display: flex;
    align-items: center;
    gap: 10px;
  }
  .brand__dot {
    width: 16px; height: 16px;
    border-radius: 50%;
    background: var(--sun-orange);
    flex: none;
  }
  .brand__name {
    color: var(--text-light);
    font-weight: 700;
    font-size: 17px;
    line-height: 1.25;
    width: 170px;
  }

  .contact {
    position: absolute;
    right: 30px;
    top: 26px;
    text-align: right;
    color: var(--text-light);
  }
  .contact__name {
    font-weight: 700;
    font-size: 18px;
    margin-bottom: 10px;
  }
  .contact__line {
    font-size: 12px;
    color: var(--text-soft);
    display: flex;
    justify-content: flex-end;
    align-items: center;
    gap: 6px;
    line-height: 1.5;
  }
  .contact__line svg { width: 11px; height: 11px; flex: none; }

  .scenery {
    position: absolute;
    right: 0;
    bottom: 0;
    width: 330px;
    height: 210px;
    background: linear-gradient(180deg, var(--sun-orange) 0%, var(--sky-blue) 35%, var(--snow) 75%);
  }

  .card--back .brand {
    left: 50%;
    top: 50%;
    transform: translate(-50%, -50%);
  }
  .card--back .brand__name {
    font-size: 20px;
    width: 210px;
    text-align: left;
  }
</style>
</head>
<body>

  <section class="card card--front" aria-label="Business card front">
    <div class="brand">
      <span class="brand__dot"></span>
      <span class="brand__name">Marrowby Water Taxi and Transport</span>
    </div>

    <div class="contact">
      <p class="contact__name">Captain Mason Elwick</p>
      <p class="contact__line">
        mason@marrowbyferryline.com
        <svg viewBox="0 0 12 12" aria-hidden="true">
          <rect x="1" y="2.5" width="10" height="7" rx="1" fill="none" stroke="#f8a13a" stroke-width="1.2"/>
          <path d="M1.5 3 L6 6.5 L10.5 3" fill="none" stroke="#f8a13a" stroke-width="1.2"/>
        </svg>
      </p>
      <p class="contact__line">
        www.marrowbyferryline.com
        <svg viewBox="0 0 12 12" aria-hidden="true">
          <circle cx="6" cy="6" r="4.6" fill="none" stroke="#c9ced6" stroke-width="1.2"/>
          <path d="M1.4 6 H10.6 M6 1.4 C3.8 4 3.8 8 6 10.6 M6 1.4 C8.2 4 8.2 8 6 10.6" fill="none" stroke="#c9ced6" stroke-width="0.9"/>
        </svg>
      </p>
    </div>

    <div class="scenery" role="img" aria-label="Illustration of snowy mountain peaks under an orange sun"></div>
  </section>

  <section class="card card--back" aria-label="Business card back">
    <div class="brand">
      <span class="brand__dot"></span>
      <span class="brand__name">Marrowby Water Taxi and Transport</span>
    </div>
  </section>

</body>
</html>
```